Real Estate investment company needs billboard designs

This is our website: https://brightlanepropertygroup.com/
We are looking for some billboard concepts that uses our CEO in the design. I have attached some images and 1 billboard design that someone in our industry uses, but we don't want it exactly like his.

Industry/Entity Type

real estate

Colors

Designer to choose colors to be used in the design.

Requirements
Must have
• Company colors from websiute

```html
<!DOCTYPE html>
<html lang="en">
<head>
<meta charset="UTF-8">
<title>Bright Lane Property Group – Billboard</title>
<link href="https://fonts.googleapis.com/css2?family=Montserrat:wght@600;700;800&display=swap" rel="stylesheet">
<style>
  :root {
    --red: #f3171b;
    --ink: #111111;
    --charcoal: #231f20;
    --paper: #ffffff;
    --backdrop: #6f6f6f;
    --denim-light: #b9cbe0;
    --denim-dark: #8ea7c4;
  }
  * { box-sizing: border-box; margin: 0; padding: 0; }
  html, body {
    width: 1071px; height: 1200px; overflow: hidden;
    background: var(--backdrop);
    font-family: "Montserrat", Arial, sans-serif;
  }
  .billboard {
    position: absolute; left: 28px; top: 365px;
    width: 1015px; height: 469px;
    background: var(--paper);
    overflow: hidden;
    box-shadow: 0 2px 8px rgba(0,0,0,.35);
  }
  .ceo-photo {
    position: absolute; left: 640px; top: 72px;
    width: 375px; height: 338px;
    background: linear-gradient(160deg, #f4f4f4 0%, var(--denim-light) 55%, var(--denim-dark) 100%);
    clip-path: polygon(235px 0, 375px 0, 375px 338px, 0 338px, 0 80px, 235px 80px);
    z-index: 0;
  }
  .tagline {
    position: absolute; left: 21px; top: 12px; z-index: 1;
    font-size: 53px; line-height: 60px; font-weight: 700; color: var(--ink);
    letter-spacing: 0.3px; white-space: nowrap;
  }
  .headline {
    position: absolute; left: 19px; top: 64px; z-index: 1;
    font-size: 80px; line-height: 84px; font-weight: 800; color: var(--red);
    letter-spacing: -1px; white-space: nowrap;
  }
  .accent-bar {
    position: absolute; left: 21px; top: 155px;
    width: 100px; height: 12px; background: var(--red);
    clip-path: polygon(0 0, 100% 0, 96% 100%, 0 100%);
  }
  .brand-name {
    position: absolute; left: 21px; top: 205px; z-index: 1;
    color: var(--ink); font-weight: 800; line-height: 1;
    text-transform: uppercase; white-space: nowrap;
  }
  .brand-name .line-main { display: block; font-size: 73px; letter-spacing: -1px; }
  .brand-name .line-sub { display: block; font-size: 45px; margin-top: 16px; letter-spacing: 1px; }
  .contact-band {
    position: absolute; left: 0; bottom: 0; width: 1015px; height: 59px; z-index: 2;
  }
  .band-shape { position: absolute; left: 0; top: 0; }
  .phone {
    position: absolute; left: 19px; top: 0; height: 59px;
    display: flex; align-items: center; gap: 12px;
    color: var(--paper); font-weight: 800; font-size: 57px; letter-spacing: -1px;
    line-height: 1; white-space: nowrap;
  }
  .phone-icon { flex: 0 0 auto; }
  .website {
    position: absolute; left: 528px; top: 0; height: 59px;
    display: flex; align-items: center; gap: 8px;
    color: var(--paper); font-weight: 700; font-size: 27px; letter-spacing: -0.3px;
    white-space: nowrap;
  }
  .globe-icon { flex: 0 0 auto; }
  .website .tld { color: var(--red); }
</style>
</head>
<body>
  <main class="billboard">
    <div class="ceo-photo" role="img" aria-label="Photo of the company CEO smiling and pointing up toward the headline, wearing a light blue denim shirt"></div>

    <p class="tagline">Get a Cash Offer, Same Day.</p>
    <h1 class="headline">Selling Your Home?</h1>
    <div class="accent-bar"></div>

    <div class="brand-name">
      <span class="line-main">Bright Lane</span>
      <span class="line-sub">Property Group</span>
    </div>

    <footer class="contact-band">
      <svg class="band-shape" width="1015" height="59" viewBox="0 0 1015 59" aria-hidden="true">
        <polygon points="0,0 488,0 518,59 0,59" fill="#f3171b"/>
        <polygon points="497,0 1015,0 1015,59 529,59" fill="#231f20"/>
      </svg>
      <div class="phone">
        <svg class="phone-icon" width="40" height="40" viewBox="0 0 24 24" aria-hidden="true">
          <path fill="#fff" d="M6.6 10.8a15.1 15.1 0 0 0 6.6 6.6l2.2-2.2a1 1 0 0 1 1-.25 11.4 11.4 0 0 0 3.6.57 1 1 0 0 1 1 1V20a1 1 0 0 1-1 1A17 17 0 0 1 3 4a1 1 0 0 1 1-1h3.5a1 1 0 0 1 1 1c0 1.25.2 2.45.57 3.57a1 1 0 0 1-.25 1z"/>
          <path fill="none" stroke="#fff" stroke-width="1.6" stroke-linecap="round" d="M14 3.5a7 7 0 0 1 6.5 6.5M14 7a3.5 3.5 0 0 1 3 3"/>
        </svg>
        <span>555-014-2290</span>
      </div>
      <div class="website">
        <svg class="globe-icon" width="34" height="34" viewBox="0 0 24 24" aria-hidden="true">
          <g fill="none" stroke="#f3171b" stroke-width="1.5">
            <circle cx="12" cy="12" r="10"/>
            <ellipse cx="12" cy="12" rx="4.5" ry="10"/>
            <path d="M2 12h20M3.5 7h17M3.5 17h17M12 2v20"/>
          </g>
        </svg>
        <span>brightlanepropertygroup<span class="tld">.com</span></span>
      </div>
    </footer>
  </main>
</body>
</html>
```